Swiftcoinswap.com Mobile App

Swiftcoinswap.com is an online Beurea de change. They buy and sell currency from individuals and large corporations.

The app will compliment the main website of the company and focus on specific features as set out in our brief document. overall the design must be high-quality, easy navigate with a one finger operation and nice clean design.

This content is for the design of 3 screen

Loading screen
Homepage screen
Buy Currency for Branch Collection screen

attached is a full brief, but the loading screen will incorporate the logo and the home screen must allow easy navigation to 6 key button features that will enable you to go to each section of the app.

The winner will get to design the remaining screens of the app which are approx 15/18 further screens, based on the same layout.

If you can code the app as well into iPhone and Android, please make this known as well.
Updates

Hello,

For further inspritation for the Home screen, we quite like the interface on the uploaded image lumavo-home.jpg

So you slide left and right with your finger to the button, instead of a list format or something quite 2d. Almost 3d like interface maybe with an option to display all as a list?

See what sort of creativity can be achieved.

thanks

Target Market(s)

Consumers mainly aged between 25-60

Industry/Entity Type

It Company

Requirements
Must have
• good clean visually stunning appearance with apply shiny effect buttons and navigation

```html
<!DOCTYPE html>
<html lang="en">
<head>
<meta charset="utf-8">
<title>Swiftcoinswap – App Screens</title>
<link rel="stylesheet" href="https://fonts.googleapis.com/css2?family=Roboto:wght@400;500;700&display=swap">
<style>
  :root {
    --stage: #262626;
    --stage-edge: #1b1b1b;
    --brand-blue: #1f5d9e;
    --brand-red: #d8283a;
    --label-blue: #4a86c0;
    --sign-pink: #d7336a;
    --ink: #333333;
    --muted: #6a6a6a;
    --metal-light: #f1f1f1;
    --metal-dark: #d2d2d2;
    --panel: #e7e7e7;
    --panel-edge: #b9b9b9;
    --white: #ffffff;
  }
  * { box-sizing: border-box; margin: 0; padding: 0; }
  html, body { width: 1200px; height: 570px; overflow: hidden; }
  body {
    background: linear-gradient(180deg, var(--stage-edge) 0 46px, var(--stage) 46px 545px, var(--stage-edge) 545px);
    font-family: "Roboto", Arial, sans-serif;
    color: var(--ink);
    position: relative;
  }
  .screen {
    position: absolute;
    top: 153px;
    width: 190px;
    height: 286px;
    overflow: hidden;
  }
  .screen--loading { left: 47px; background: linear-gradient(135deg, #ffffff 0%, #f3f3f3 55%, #e2e2e2 100%); }
  .screen--login { left: 357px; background: radial-gradient(circle at 50% 40%, #ececec, #d9d9d9); }
  .screen--home { left: 667px; }
  .screen--feature { left: 977px; }
  .screen--home, .screen--feature {
    background: repeating-linear-gradient(180deg, var(--metal-light) 0 2px, #e6e6e6 2px 3px);
  }

  /* Brand name lockup */
  .brand {
    position: absolute;
    left: 0; right: 0;
    display: flex;
    align-items: center;
    justify-content: center;
    gap: 6px;
  }
  .brand__dot { width: 12px; height: 12px; border-radius: 50%; background: var(--brand-red); }
  .brand__name { font-weight: 700; color: var(--brand-blue); font-size: 22px; letter-spacing: -0.5px; }
  .screen--loading .brand { top: 128px; }
  .screen--login .brand { top: 74px; }
  .screen--home .brand, .screen--feature .brand { top: 22px; }

  /* Loading bar */
  .progress {
    position: absolute; left: 4px; right: 4px; top: 270px; height: 12px;
    border: 1px solid #9aa9b8; border-radius: 3px;
    background: repeating-linear-gradient(-45deg, var(--brand-blue) 0 6px, var(--white) 6px 11px);
  }

  /* Login */
  .login-form {
    position: absolute; left: 6px; right: 6px; top: 148px; height: 58px;
    background: rgba(255,255,255,0.35); border: 1px solid #c8c8c8;
    padding: 4px 6px 0 10px;
  }
  .field { display: flex; align-items: center; justify-content: space-between; height: 24px; }
  .field__label { color: var(--label-blue); font-weight: 700; font-size: 13px; }
  .field__input { width: 86px; height: 19px; background: var(--white); border: 1px solid #9c9c9c; }
  .button {
    position: absolute; left: 19px; width: 155px; height: 24px;
    background: linear-gradient(180deg, #ffffff, #e3e3e3);
    border: 1px solid #a8a8a8; border-radius: 2px;
    display: flex; align-items: center; justify-content: center;
    font-size: 12px; font-weight: 500;
    box-shadow: 0 1px 2px rgba(0,0,0,0.25);
  }
  .button--sign-in { top: 210px; color: var(--sign-pink); }
  .button--create { top: 245px; color: var(--muted); }

  /* Home panel */
  .panel {
    position: absolute; left: 6px; right: 6px; top: 85px; height: 165px;
    border: 1px solid var(--panel-edge); border-radius: 10px;
    background: linear-gradient(180deg, #f4f4f4, var(--panel));
    box-shadow: inset 0 1px 0 var(--white);
  }
  .menu { display: grid; grid-template-columns: repeat(3, 54px); justify-content: center; column-gap: 2px; row-gap: 4px; padding-top: 11px; }
  .menu__item { display: flex; flex-direction: column; align-items: center; }
  .orb {
    width: 46px; height: 46px; border-radius: 50%;
    background: radial-gradient(circle at 50% 30%, #ffffff 0%, #e2e2e2 55%, #bdbdbd 100%);
    border: 1px solid #a9a9a9;
    box-shadow: 0 1px 3px rgba(0,0,0,0.3);
    display: flex; align-items: center; justify-content: center;
    color: #333; font-weight: 700; font-size: 22px;
  }
  .orb svg { width: 24px; height: 24px; }
  .menu__label { font-size: 6px; color: var(--muted); text-align: center; margin-top: 3px; line-height: 1.2; height: 15px; }

  /* Tab bar */
  .tabbar { position: absolute; left: 0; right: 0; top: 252px; height: 34px; }
  .tab {
    position: absolute; border-radius: 50%;
    background: radial-gradient(circle at 50% 30%, #ffffff, #d6d6d6 70%, #b4b4b4);
    border: 1px solid #9d9d9d;
    display: flex; align-items: center; justify-content: center;
  }
  .tab--fav { left: 2px; top: 5px; width: 22px; height: 22px; }
  .tab--home { left: 80px; top: 1px; width: 31px; height: 31px; }
  .tab--info { right: 2px; top: 5px; width: 22px; height: 22px; font: italic 700 12px Georgia, serif; color: #333; }
  .tab svg { width: 13px; height: 13px; }
  .tab--home svg { width: 17px; height: 17px; }

  /* Feature detail */
  .feature-title {
    position: absolute; left: 12px; right: 10px; top: 15px; height: 34px;
    display: flex; align-items: center;
  }
  .feature-title__orb {
    width: 34px; height: 34px; border-radius: 50%;
    background: radial-gradient(circle at 50% 30%, #6fa6dc, #1f5d9e 70%);
    border: 1px solid #1a4a7c;
    display: flex; align-items: center; justify-content: center; z-index: 1;
  }
  .feature-title__orb svg { width: 20px; height: 20px; }
  .feature-title__pill {
    margin-left: -6px; height: 20px; flex: 1;
    background: linear-gradient(180deg, #ffffff, #e6e6e6);
    border: 1px solid #c4c4c4; border-radius: 0 4px 4px 0;
    padding-left: 14px; display: flex; align-items: center;
    font-size: 11px; font-weight: 500; color: #444;
  }
  .feature-copy { position: absolute; left: 12px; right: 10px; top: 64px; font-size: 5.6px; line-height: 1.35; color: #444; }
  .feature-copy p + p { margin-top: 6px; }
  .pager {
    position: absolute; right: 8px; top: 134px; width: 60px; height: 16px;
    background: linear-gradient(180deg, #fafafa, #e0e0e0); border: 1px solid #c4c4c4; border-radius: 8px;
    display: flex; justify-content: space-between; align-items: center;
  }
  .pager__arrow {
    width: 15px; height: 15px; border-radius: 50%;
    background: radial-gradient(circle at 50% 30%, #fff, #cfcfcf); border: 1px solid #a5a5a5;
    display: flex; align-items: center; justify-content: center;
  }
  .pager__arrow svg { width: 9px; height: 9px; }
</style>
</head>
<body>

<!-- Loading screen -->
<section class="screen screen--loading" aria-label="Loading screen">
  <div class="brand"><span class="brand__dot"></span><span class="brand__name">Swiftcoinswap</span></div>
  <div class="progress" aria-label="Loading"></div>
</section>

<!-- Login screen -->
<section class="screen screen--login" aria-label="Sign in screen">
  <div class="brand"><span class="brand__dot"></span><span class="brand__name">Swiftcoinswap</span></div>
  <div class="login-form">
    <div class="field"><span class="field__label">Username</span><span class="field__input"></span></div>
    <div class="field"><span class="field__label">Password</span><span class="field__input"></span></div>
  </div>
  <div class="button button--sign-in">Sign In</div>
  <div class="button button--create">Create New Account</div>
</section>

<!-- Home screen -->
<section class="screen screen--home" aria-label="Home screen">
  <div class="brand"><span class="brand__dot"></span><span class="brand__name">Swiftcoinswap</span></div>
  <div class="panel">
    <div class="menu">
      <div class="menu__item">
        <div class="orb"><svg viewBox="0 0 24 24"><path d="M4 5l8 7-8 7zM12 5l8 7-8 7z" fill="#333"/></svg></div>
        <div class="menu__label">Fast<br>Track</div>
      </div>
      <div class="menu__item">
        <div class="orb">$</div>
        <div class="menu__label">Buy<br>Currency</div>
      </div>
      <div class="menu__item">
        <div class="orb"><svg viewBox="0 0 24 24"><circle cx="10" cy="10" r="6" fill="none" stroke="#333" stroke-width="3"/><path d="M14.5 14.5L21 21" stroke="#333" stroke-width="4" stroke-linecap="round"/></svg></div>
        <div class="menu__label">Locate<br>Stores</div>
      </div>
      <div class="menu__item">
        <div class="orb" style="font-size:14px">$<svg viewBox="0 0 24 24" style="width:12px;height:12px"><path d="M3 9h15l-4-4M21 15H6l4 4" fill="none" stroke="#333" stroke-width="2.5"/></svg>£</div>
        <div class="menu__label">Converter</div>
      </div>
      <div class="menu__item">
        <div class="orb"><svg viewBox="0 0 24 24"><path d="M8 20V5M4 9l4-4 4 4M16 4v15M12 15l4 4 4-4" fill="none" stroke="#333" stroke-width="2.5"/></svg></div>
        <div class="menu__label">Live Rates</div>
      </div>
      <div class="menu__item">
        <div class="orb"><svg viewBox="0 0 24 24"><circle cx="12" cy="12" r="7" fill="none" stroke="#333" stroke-width="4" stroke-dasharray="3 2.5"/><circle cx="12" cy="12" r="5.5" fill="none" stroke="#333" stroke-width="3"/></svg></div>
        <div class="menu__label">Preferences</div>
      </div>
    </div>
  </div>
  <nav class="tabbar">
    <span class="tab tab--fav"><svg viewBox="0 0 24 24"><path d="M12 2l3 7h7l-5.5 4.5 2 7.5L12 16.5 5.5 21l2-7.5L2 9h7z" fill="#333"/></svg></span>
    <span class="tab tab--home"><svg viewBox="0 0 24 24"><path d="M12 3L2 12h3v9h5v-6h4v6h5v-9h3z" fill="#333"/></svg></span>
    <span class="tab tab--info">i</span>
  </nav>
</section>

<!-- Locate Stores screen -->
<section class="screen screen--feature" aria-label="Locate stores screen">
  <div class="brand"><span class="brand__dot"></span><span class="brand__name">Swiftcoinswap</span></div>
  <div class="panel">
    <div class="feature-title">
      <span class="feature-title__orb"><svg viewBox="0 0 24 24"><circle cx="10" cy="10" r="6" fill="none" stroke="#1b2b3c" stroke-width="3"/><path d="M14.5 14.5L21 21" stroke="#1b2b3c" stroke-width="4" stroke-linecap="round"/></svg></span>
      <span class="feature-title__pill">Locate Stores</span>
    </div>
    <div class="feature-copy">
      <p>This function allows you to locate the stores close to you. And some more text to describe the function further can be added here.</p>
      <p>This function allows you to locate the stores close to you. And some more text to describe the function further can be added here.</p>
    </div>
    <div class="pager">
      <span class="pager__arrow"><svg viewBox="0 0 24 24"><path d="M20 12H5M11 5l-7 7 7 7" fill="none" stroke="#333" stroke-width="4"/></svg></span>
      <span class="pager__arrow"><svg viewBox="0 0 24 24"><path d="M4 12h15M13 5l7 7-7 7" fill="none" stroke="#333" stroke-width="4"/></svg></span>
    </div>
  </div>
  <nav class="tabbar">
    <span class="tab tab--fav"><svg viewBox="0 0 24 24"><path d="M12 2l3 7h7l-5.5 4.5 2 7.5L12 16.5 5.5 21l2-7.5L2 9h7z" fill="#333"/></svg></span>
    <span class="tab tab--home"><svg viewBox="0 0 24 24"><path d="M12 3L2 12h3v9h5v-6h4v6h5v-9h3z" fill="#333"/></svg></span>
    <span class="tab tab--info">i</span>
  </nav>
</section>

</body>
</html>
```